I have a website called Okenta Holdings (okentaholdings.com) that I would like to have redesigned. Most of the content is already created, but I need a new design. You can also see my other website at brambleacres.com. I am open to a new logo or modifying the current logo if you have a good idea. Please feel free to use other images for the home page (and maybe some other locations) if you feel they provide a better look and feel to the website. I prefer a modern look.

Important: You do not have to use the images I've provided for the home page. Feel free to find your own stock photos. You don't have to pay for them unless I select your design.

1) Please use wix.com to make your changes so that I can edit it later.
2) I will need all the graphics files to be saved so I can dowload it for later.
3) I will be adding more content to the site later.
4) This site will likely be transferred over to brambleacres.com so if you make a logo please make one for Okenta Holdings and one for Bramble Acres.
5) You can use other images that you feel would help the look and feel of the website.

```html
<!DOCTYPE html>
<html lang="en">
<head>
<meta charset="utf-8">
<title>Okenta Holdings — Private Commercial Real Estate</title>
<link href="https://fonts.googleapis.com/css2?family=Roboto:wght@300;400;500;700&display=swap" rel="stylesheet">
<style>
:root{
  --navy:#0c2d55;
  --navy-deep:#0a2748;
  --blue:#4a8fd8;
  --blue-soft:#5c9be0;
  --ice:#c6dcf3;
  --mist:#eef3fa;
  --ink:#333b45;
  --grey:#6a6f76;
  --line:#d7dbe0;
  --white:#ffffff;
}
*{box-sizing:border-box;margin:0;padding:0}
html,body{width:1200px;height:3771px;overflow:hidden}
body{font-family:"Roboto",Arial,sans-serif;color:var(--ink);background:var(--white);position:relative}
section,header,footer{position:absolute;left:0;width:1200px}

/* header */
.site-header{top:0;height:108px;background:var(--navy)}
.brand{position:absolute;left:0;top:0;width:395px;height:108px;background:var(--white);display:flex;align-items:center;padding-left:112px;gap:14px}
.brand-mark{width:40px;height:40px;background:var(--blue);border-radius:6px}
.brand-name{font-size:27px;font-weight:500;color:var(--blue)}
.nav{position:absolute;left:395px;top:0;height:108px;display:flex;align-items:center}
.nav a{color:var(--white);font-size:13px;font-weight:500;text-decoration:none;height:108px;display:flex;align-items:center;padding:0 27px}
.nav a.active{color:var(--blue-soft);border-bottom:3px solid var(--blue-soft)}
.login{position:absolute;left:978px;top:31px;width:111px;height:45px;border-radius:23px;background:var(--blue);display:flex;align-items:center;gap:14px;padding-left:6px;color:var(--white);font-size:13px;font-weight:500}
.login span.icon{width:33px;height:33px;border-radius:50%;background:var(--navy);display:flex;align-items:center;justify-content:center}

/* hero */
.hero{top:108px;height:719px;background:linear-gradient(180deg,#7a78b8 0%,#c79a8a 35%,#e7a25a 55%,#5b5a52 75%,#2f3b2e 100%)}
.hero-text{position:absolute;top:120px;width:100%;text-align:center}
.hero h1{font-size:48px;font-weight:500;color:var(--white)}
.hero h2{font-size:37px;font-weight:500;color:var(--white);margin-top:4px}
.hero p{font-size:25px;font-weight:500;color:var(--navy);margin-top:14px}
.dots{position:absolute;top:690px;left:0;width:100%;display:flex;justify-content:center;gap:7px}
.dots i{width:11px;height:11px;border-radius:50%;background:var(--white)}
.dots i.on{background:var(--blue)}

/* services */
.services{top:827px;height:586px}
.card{position:absolute;top:79px;width:311px;height:430px;background:var(--white);box-shadow:0 0 6px rgba(0,0,0,.15);text-align:center;padding-top:30px}
.card svg{display:block;margin:0 auto}
.card h3{font-size:23px;font-weight:500;color:var(--ink);margin-top:26px}
.rule{width:44px;height:3px;background:var(--navy);margin:16px auto}
.card p{font-size:14px;line-height:26px;color:var(--grey);padding:0 34px}
.pill{display:inline-block;background:var(--blue);color:var(--white);font-size:14px;font-weight:500;border-radius:24px;padding:15px 23px;margin-top:26px}

/* about */
.about{top:1413px;height:514px;background:linear-gradient(180deg,#c4d9f1,#b7cfea);text-align:center}
.about h2{font-size:62px;font-weight:700;color:var(--navy);margin-top:74px}
.about .rule{width:48px;margin-top:14px}
.about p{width:670px;margin:24px auto 0;font-size:15px;font-weight:300;line-height:30px;color:var(--ink)}
.btn-dark{display:inline-block;background:var(--navy);color:var(--white);font-size:16px;font-weight:500;border-radius:30px;padding:18px 42px;margin-top:30px}

/* partners */
.partners{top:1927px;height:331px;text-align:center}
.section-title{font-size:41px;font-weight:700;color:var(--navy)}
.partners .section-title{margin-top:66px}
.partner-row{position:absolute;top:165px;left:136px;display:flex;gap:22px}
.partner{width:168px;height:90px;border:1px solid var(--line);display:flex;align-items:center;justify-content:center}
.partner i{width:96px;height:22px;background:#b9bdc2;border-radius:3px}

/* testimonials */
.testimonials{top:2258px;height:390px;background:var(--mist);text-align:center}
.testimonials .section-title{margin-top:60px}
.quote{width:680px;margin:22px auto 0;font-size:13.5px;line-height:27.5px;color:var(--grey)}
.author{font-size:19px;font-weight:500;color:var(--navy);margin-top:24px}
.role{font-size:14px;color:var(--grey);margin-top:4px}
.arrow{position:absolute;top:160px;width:72px;height:72px;border:1.5px solid #8a9099;border-radius:50%;display:flex;align-items:center;justify-content:center}

/* contact */
.contact{top:2648px;height:761px;background:var(--navy-deep)}
.contact .section-title{color:var(--white);text-align:center;margin-top:40px;font-size:38px}
.contact .rule{background:var(--white);width:48px}
.field{position:absolute;height:45px;border:1px solid #c9d2dc;color:var(--white);font-size:13px;font-weight:500;padding:14px 15px}
.submit{position:absolute;left:525px;top:370px;width:150px;height:53px;border-radius:27px;background:var(--blue);color:var(--white);font-size:17px;font-weight:500;display:flex;align-items:center;justify-content:center}
.map{position:absolute;left:234px;top:449px;width:733px;height:261px;background:linear-gradient(135deg,#e8ecef,#dfe6ea 60%,#d7e6da)}

/* footer */
.site-footer{top:3409px;height:362px;background:var(--navy);color:var(--white)}
.col{position:absolute;top:52px}
.col h4{font-size:24px;font-weight:500}
.col .bar{width:36px;height:3px;background:var(--blue);margin:10px 0 24px}
.col p{font-size:13.5px;line-height:26px}
.info{display:flex;gap:14px;align-items:flex-start;margin-bottom:14px}
.foot-brand{display:flex;align-items:center;gap:12px;margin-top:26px}
.foot-brand .brand-mark{width:36px;height:36px}
.foot-brand span{font-size:30px;font-weight:500}
.copy{position:absolute;top:331px;width:100%;text-align:center;font-size:15px}
</style>
</head>
<body>

<header class="site-header">
  <div class="brand"><div class="brand-mark"></div><span class="brand-name">Okenta Holdings</span></div>
  <nav class="nav">
    <a class="active">HOME</a><a>ABOUT</a><a>STRATEGY</a><a>PROJECTS</a><a>CONTACT</a>
  </nav>
  <div class="login"><span class="icon"><svg width="14" height="16" viewBox="0 0 14 16" fill="none" stroke="#fff" stroke-width="1.5"><circle cx="7" cy="4.5" r="3.3"/><path d="M1 15c0-3.5 2.7-5.5 6-5.5s6 2 6 5.5z"/></svg></span>LOGIN</div>
</header>

<section class="hero" role="img" aria-label="City skyline at sunset with a bay bridge in the distance">
  <div class="hero-text">
    <h1>Private Commercial Real Estate</h1>
    <h2>Investment &amp; Development Firm</h2>
    <p>Building together. Growing Together</p>
  </div>
  <div class="dots"><i></i><i class="on"></i><i></i></div>
</section>

<section class="services">
  <article class="card" style="left:111px">
    <svg width="96" height="96" viewBox="0 0 96 96" fill="none" stroke="#4a8fd8" stroke-width="4"><path d="M4 22V4h18M74 4h18v18M92 74v18H74M22 92H4V74"/><circle cx="48" cy="48" r="26"/><path d="M48 12v20M48 64v20M12 48h20M64 48h20"/></svg>
    <h3>Investment Focus</h3><div class="rule"></div>
    <p>Bramble Acres evaluates opportunities with a two-pronged approach. First, the firm searches for development opportunities which are in growing metropolitan markets</p>
    <span class="pill">READ MORE</span>
  </article>
  <article class="card" style="left:445px">
    <svg width="96" height="96" viewBox="0 0 96 96" fill="none" stroke="#4a8fd8" stroke-width="4"><rect x="4" y="10" width="88" height="74" rx="6"/><path d="M4 28h88"/><circle cx="14" cy="19" r="2" fill="#4a8fd8"/><circle cx="22" cy="19" r="2" fill="#4a8fd8"/><circle cx="30" cy="19" r="2" fill="#4a8fd8"/><path d="M34 46l-10 10 10 10M62 46l10 10-10 10M54 42l-12 28"/></svg>
    <h3>Development</h3><div class="rule"></div>
    <p>Bramble Acres evaluates opportunities with a two-pronged approach. First, the firm searches for development opportunities which are in growing metropolitan markets</p>
    <span class="pill">READ MORE</span>
  </article>
  <article class="card" style="left:778px">
    <svg width="96" height="96" viewBox="0 0 96 96" fill="none" stroke="#4a8fd8" stroke-width="4"><path d="M52 8h30v30L40 80 10 50z"/><circle cx="70" cy="20" r="5"/><path d="M26 50l16-16M32 56l16-16M38 62l16-16"/><path d="M74 16c8-8 16-4 14 6"/></svg>
    <h3>Product Types</h3><div class="rule"></div>
    <p>Bramble Acres evaluates opportunities with a two-pronged approach. First, the firm searches for development opportunities which are in growing metropolitan markets</p>
    <span class="pill">READ MORE</span>
  </article>
</section>

<section class="about">
  <h2>ABOUT US</h2><div class="rule"></div>
  <p>Bramble Acres is a private real estate firm that specializes in the procurement, development, management, and disposition of various commercial real estate asset types including multifamily, industrial, single-family, hospitality, self-storage, and flex. The firm effectuates its strategy utilizing long-standing relationships to ascertain acquisition and development opportunities within a specific target market.&nbsp; Bramble Acres is currently focused on acquisition and development opportunities in the southern portion of the United States.</p>
  <span class="btn-dark">READ MORE</span>
</section>

<section class="partners">
  <h2 class="section-title">CORPORATE PARTNERS</h2><div class="rule" style="width:48px"></div>
  <div class="partner-row">
    <div class="partner"><i></i></div><div class="partner"><i></i></div><div class="partner"><i></i></div><div class="partner"><i></i></div><div class="partner"><i></i></div>
  </div>
</section>

<section class="testimonials">
  <h2 class="section-title">TESTIMONIALS</h2><div class="rule" style="width:48px"></div>
  <div class="arrow" style="left:136px"><svg width="14" height="22" viewBox="0 0 14 22" fill="none" stroke="#555" stroke-width="2"><path d="M12 2L3 11l9 9"/></svg></div>
  <div class="arrow" style="left:993px"><svg width="14" height="22" viewBox="0 0 14 22" fill="none" stroke="#555" stroke-width="2"><path d="M2 2l9 9-9 9"/></svg></div>
  <p class="quote">&ldquo; After spending years working for various real estate development and private equity firms, Daniel Whitcombe formed Bramble Acres in 2017 to fulfill his lifelong ambition of starting his own firm to acquire and develop unique Class A real estate opportunities in major metropolitan markets that provide strong risk adjusted returns. The core belief of the firm is centered around a profound moral and ethical duty to properly manage the relationships and assets of our partners, clients, and customers at the firm. &rdquo;</p>
  <div class="author">Daniel Whitcombe</div>
  <div class="role">Founder &amp; CEO</div>
</section>

<section class="contact">
  <h2 class="section-title">CONTACT US</h2><div class="rule"></div>
  <div class="field" style="left:291px;top:135px;width:299px">First Name :</div>
  <div class="field" style="left:609px;top:135px;width:300px">Last Name :</div>
  <div class="field" style="left:291px;top:193px;width:299px">Email :</div>
  <div class="field" style="left:609px;top:193px;width:300px">Subject :</div>
  <div class="field" style="left:291px;top:251px;width:618px;height:97px">Message :</div>
  <div class="submit">SUBMIT</div>
  <div class="map" role="img" aria-label="Street map of the downtown district showing the office location"></div>
</section>

<footer class="site-footer">
  <div class="col" style="left:136px;width:300px">
    <h4>Inquiries</h4><div class="bar"></div>
    <p style="padding-left:3px">For any inquiries, questions or commendations, please call: (555) 013-2750 or fill out the following form</p>
    <div class="foot-brand"><div class="brand-mark"></div><span>Okenta Holdings</span></div>
  </div>
  <div class="col" style="left:485px;width:260px">
    <h4>Headquarters</h4><div class="bar"></div>
    <div class="info"><svg width="11" height="15" viewBox="0 0 11 15"><path d="M5.5 0A5.5 5.5 0 0 0 0 5.5C0 9.5 5.5 15 5.5 15S11 9.5 11 5.5A5.5 5.5 0 0 0 5.5 0zm0 7.5a2 2 0 1 1 0-4 2 2 0 0 1 0 4z" fill="#4a8fd8"/></svg><p>480 Larkspur Ave. 7th Floor<br>Fairview, Texas 75069</p></div>
    <div class="info" style="margin-top:14px"><svg width="13" height="10" viewBox="0 0 13 10"><rect width="13" height="10" rx="1" fill="#4a8fd8"/><path d="M0 1l6.5 5L13 1" stroke="#0c2d55" fill="none"/></svg><p style="line-height:12px">info@brambleacres.com</p></div>
    <div class="info"><svg width="12" height="12" viewBox="0 0 12 12"><path d="M2.5 0l2 3-1.2 1.3c.8 1.8 2.3 3.3 4.4 4.4L9 7.5l3 2-1.5 2.5C5 11.5.5 7 0 1.5z" fill="#4a8fd8"/></svg><p style="line-height:12px">Tel: (555) 013-2750</p></div>
  </div>
  <div class="col" style="left:797px;width:300px">
    <h4>Employment</h4><div class="bar"></div>
    <p style="padding-left:3px">To apply for a job with Bramble Acres, please send a cover letter together with your C.V. to: info@brambleacres.com</p>
  </div>
  <div class="copy">©2022 Okenta Holdings.All rights reserved.</div>
</footer>

</body>
</html>
```